PlumVesta screens tidy up

We would like advice on how to better present the following home page and overview pages.

The existing website is functional, but the pages don't appear professionals and pleasing to the eye. We would specifically like feedback on alignment and padding of icons and text to make the screen more appealing and polished.

We are following the quartzline design system.

1 page

Sans Serif
• IBM Plex, Poppins

```html
<!DOCTYPE html>
<html lang="en">
<head>
<meta charset="utf-8">
<title>PlumVesta – Home and Overview screens</title>
<link href="https://fonts.googleapis.com/css2?family=Poppins:wght@400;500;600;700;800&display=swap" rel="stylesheet">
<style>
:root{
  --gold:#BA853B;
  --gold-card:#B8843D;
  --tan-light:#D1A874;
  --brown:#8F6934;
  --ink:#231F20;
  --white:#FFFFFF;
  --folder:#F7C548;
  --alert:#E5383B;
}
*{box-sizing:border-box;margin:0;padding:0}
html,body{width:1014px;height:1200px;overflow:hidden;background:var(--white);font-family:"Poppins",sans-serif;color:var(--ink)}
.screen{position:absolute;left:20px;width:974px;height:548px;background:var(--gold)}
.screen--home{top:43px}
.screen--overview{top:611px}
.app{position:absolute;left:19px;top:16px;width:937px;height:515px;background:var(--white);border-radius:10px;overflow:hidden}
.topbar{position:absolute;left:0;top:0;width:100%;height:48px;background:var(--ink);display:flex;align-items:center;padding-left:26px;gap:9px}
.brand-dot{width:24px;height:24px;border-radius:50%;background:var(--gold)}
.brand-name{color:var(--white);font-size:17px;font-weight:500}

.sidebar{position:absolute;left:19px;top:50px;width:224px;display:flex;flex-direction:column}
.nav-item{display:flex;align-items:center;height:38px;background:var(--brown);color:var(--white);font-size:11.5px;padding-left:14px;margin-bottom:3px;position:relative}
.nav-item .ico{width:14px;height:14px;margin-right:15px;flex:none}
.nav-item--home{height:44px;font-size:13px;font-weight:700}
.nav-item--active{background:var(--tan-light)}
.nav-item--group{background:var(--gold);height:35px;font-size:12px;margin-bottom:0}
.nav-item--campaign{background:var(--ink);height:46px;font-size:13px;font-weight:700}
.nav-item--campaign .ico{width:20px;height:18px;margin-right:14px}
.nav-item--sub{padding-left:45px}
.nav-item--plain{font-weight:400;font-size:12px;height:35px}
.nav-item .trail{position:absolute;right:10px;top:50%;transform:translateY(-50%)}

.page-head{position:absolute;left:243px;top:50px;width:694px;height:44px;background:var(--gold)}
.page-title{position:absolute;left:347px;top:50%;transform:translate(-50%,-50%);font-size:26px;font-weight:800;letter-spacing:.5px}
.page-crumb{position:absolute;left:38px;top:50%;transform:translateY(-50%);font-size:11.5px}

.panel{position:absolute;left:252px;top:105px;width:672px;height:395px;background:var(--ink);border-radius:12px}
.label{position:absolute;color:var(--white);font-size:10px;font-weight:700;transform:translateY(-50%)}
.team-box{position:absolute;left:29px;width:624px;height:61px;background:var(--white);padding:10px 23px}
.team-name{color:var(--gold-card);font-size:17px;font-weight:700;line-height:1.3}
.team-desc{font-size:11px;line-height:1.4}
.card{position:absolute;width:310px;background:var(--gold-card)}
.card--l{left:28px}
.card--r{left:342px}
.at{position:absolute;white-space:nowrap}
.c{transform:translateX(-50%);text-align:center}
.mid{transform:translateY(-50%)}
.cm{transform:translate(-50%,-50%);text-align:center}
.big{font-size:26px;font-weight:700;line-height:1}
.big--w{color:var(--white)}
.h16{font-size:16px;font-weight:700}
.usage-bar{position:absolute;left:10px;top:56px;width:290px;height:29px;background:var(--white);font-size:11px;display:flex;align-items:center;justify-content:center}
.new-btn{position:absolute;left:536px;top:254px;width:106px;height:24px;background:var(--white);font-size:10px;display:flex;align-items:center;justify-content:center;gap:6px}
.small{font-size:11px}
.tiny{font-size:8px}
.bold10{font-size:10px;font-weight:700}
</style>
</head>
<body>

<svg width="0" height="0" style="position:absolute">
  <defs>
    <symbol id="i-home" viewBox="0 0 16 16"><path d="M2 8 8 2.5 14 8M4 7v6.5h3V10h2v3.5h3V7" fill="none" stroke="currentColor" stroke-width="1.3"/></symbol>
    <symbol id="i-bell" viewBox="0 0 16 16"><path d="M8 2a4 4 0 0 0-4 4v4l-1.5 2h11L12 10V6a4 4 0 0 0-4-4zM6.5 13.5a1.5 1.5 0 0 0 3 0z" fill="currentColor"/></symbol>
    <symbol id="i-gear" viewBox="0 0 16 16"><circle cx="8" cy="8" r="4.3" fill="none" stroke="currentColor" stroke-width="3" stroke-dasharray="2.2 1.2"/><circle cx="8" cy="8" r="3" fill="currentColor"/><circle cx="8" cy="8" r="1.3" fill="var(--brown)"/></symbol>
    <symbol id="i-files" viewBox="0 0 24 20"><rect x="11" y="1" width="10" height="13" fill="#DCE6F2" stroke="#3B82C4"/><rect x="8" y="3" width="10" height="13" fill="#F2F2F2" stroke="#999"/><path d="M1 7h6l2 2h9v10H1z" fill="var(--folder)"/><rect x="3" y="15" width="5" height="2" fill="#8A6A1F"/></symbol>
    <symbol id="i-folder" viewBox="0 0 24 20"><path d="M1 3h8l2 2h12v14H1z" fill="#F0B93A"/><path d="M1 7h22v12H1z" fill="var(--folder)"/></symbol>
    <symbol id="i-clock" viewBox="0 0 24 24"><circle cx="12" cy="12" r="11" fill="#F4C34E"/><circle cx="12" cy="12" r="8.5" fill="#fff"/><path d="M12 6v6l-3 3" stroke="#2B5DA8" stroke-width="1.6" fill="none"/></symbol>
    <symbol id="i-bars" viewBox="0 0 20 18"><rect x="1" y="10" width="4" height="8" fill="currentColor"/><rect x="8" y="5" width="4" height="13" fill="currentColor"/><rect x="15" y="0" width="4" height="18" fill="currentColor"/></symbol>
    <symbol id="i-people" viewBox="0 0 30 22"><circle cx="15" cy="5" r="3.5" fill="currentColor"/><path d="M9 21a6 6 0 0 1 12 0z" fill="currentColor"/><circle cx="6" cy="8" r="3" fill="currentColor"/><path d="M0 20a6 6 0 0 1 9-5l-1 5z" fill="currentColor"/><circle cx="24" cy="8" r="3" fill="currentColor"/><path d="M30 20a6 6 0 0 0-9-5l1 5z" fill="currentColor"/></symbol>
    <symbol id="i-tree" viewBox="0 0 24 24"><rect x="9" y="1" width="6" height="5" fill="currentColor"/><path d="M12 6v4M4 10h16M4 10v4M12 10v4M20 10v4" stroke="currentColor" stroke-width="2" fill="none"/><rect x="1" y="14" width="6" height="5" fill="currentColor"/><rect x="9" y="14" width="6" height="5" fill="currentColor"/><rect x="17" y="14" width="6" height="5" fill="currentColor"/><rect x="1" y="21" width="22" height="2" fill="currentColor"/></symbol>
    <symbol id="i-cubes" viewBox="0 0 24 22"><path d="M12 1l5 2.5v5L12 11 7 8.5v-5zM7 11l5 2.5v5L7 21l-5-2.5v-5zM17 11l5 2.5v5L17 21l-5-2.5v-5z" fill="none" stroke="currentColor" stroke-width="1"/></symbol>
    <symbol id="i-warn" viewBox="0 0 24 22"><path d="M12 1 23 21H1z" fill="var(--alert)"/><rect x="11" y="7" width="2" height="8" fill="#fff"/><rect x="11" y="16.5" width="2" height="2" fill="#fff"/></symbol>
    <symbol id="i-chev-up" viewBox="0 0 12 8"><path d="M1 7 6 2l5 5" stroke="#fff" fill="none" stroke-width="1"/></symbol>
    <symbol id="i-chev-down" viewBox="0 0 12 8"><path d="M1 1l5 5 5-5" stroke="#fff" fill="none" stroke-width="1"/></symbol>
  </defs>
</svg>

<!-- Home screen -->
<section class="screen screen--home">
  <div class="app">
    <header class="topbar"><span class="brand-dot"></span><span class="brand-name">PlumVesta</span></header>
    <nav class="sidebar">
      <div class="nav-item nav-item--home nav-item--active"><svg class="ico" style="color:var(--gold)"><use href="#i-home"/></svg>HOME</div>
      <div class="nav-item"><svg class="ico"><use href="#i-bell"/></svg>ALL ALERTS</div>
      <div class="nav-item" style="margin-bottom:0"><svg class="ico"><use href="#i-gear"/></svg>MANAGE</div>
      <div class="nav-item nav-item--group" style="padding-left:43px">Campaigns<span class="trail" style="font-weight:700;font-size:14px">+</span></div>
      <div class="nav-item nav-item--campaign"><svg class="ico"><use href="#i-files"/></svg>MY CUSTOM CAMPAIGN<svg class="trail" width="11" height="7"><use href="#i-chev-up"/></svg></div>
      <div class="nav-item nav-item--sub">OVERVIEW</div>
      <div class="nav-item nav-item--sub">FILE &amp; HONEYTOKENS</div>
      <div class="nav-item nav-item--sub">RESOURCES</div>
      <div class="nav-item nav-item--sub">ALERTS</div>
      <div class="nav-item nav-item--sub" style="margin-bottom:6px">SETTINGS</div>
      <div class="nav-item nav-item--campaign nav-item--plain"><svg class="ico"><use href="#i-files"/></svg>Default Campaign<svg class="trail" width="11" height="7"><use href="#i-chev-down"/></svg></div>
    </nav>
    <div class="page-head"><span class="page-title">HOME</span></div>
    <main class="panel">
      <span class="label" style="left:29px;top:26px">TEAMSPACE</span>
      <div class="team-box" style="top:46px"><div class="team-name">DEFAULT</div><div class="team-desc">The default client is create as apart of your user account</div></div>

      <span class="label" style="left:29px;top:136px">SUBSCRIPTION OVERVIEW</span>
      <span class="label" style="left:343px;top:136px">FILES &amp; HONEYTOKENS</span>
      <div class="card card--l" style="top:153px;height:94px">
        <svg class="at c" style="left:155px;top:8px" width="20" height="18"><use href="#i-bars"/></svg>
        <span class="at cm h16" style="left:155px;top:40px">STARTER PACK USAGE</span>
        <div class="usage-bar">0 files active out of 10 allowed</div>
      </div>
      <div class="card card--r" style="top:153px;height:94px">
        <svg class="at" style="left:63px;top:20px" width="27" height="27"><use href="#i-clock"/></svg>
        <span class="at big big--w" style="left:94px;top:24px">0</span>
        <svg class="at" style="left:196px;top:20px" width="29" height="25"><use href="#i-folder"/></svg>
        <span class="at big big--w" style="left:231px;top:24px">30</span>
        <span class="at cm h16" style="left:155px;top:72px">STATISTICS</span>
      </div>

      <span class="label" style="left:29px;top:272px">SUBSCRIPTION OVERVIEW</span>
      <div class="new-btn">NEW CAMPAIGN <span>+</span></div>

      <div class="card card--l" style="top:290px;height:94px">
        <svg class="at" style="left:12px;top:24px" width="46" height="40"><use href="#i-files"/></svg>
        <span class="at cm h16" style="left:180px;top:20px">MY CUSTOM CAMPAIGN</span>
        <span class="at cm small" style="left:180px;top:39px">this is my custom campaign for finding i</span>
        <span class="at big big--w mid" style="left:74px;top:63px">0</span>
        <span class="at small mid" style="left:98px;top:55px">Active</span>
        <span class="at mid" style="left:98px;top:68px;font-size:12px;font-weight:700;color:var(--white)">FILES AND HONEYTOKENS</span>
        <span class="at cm tiny" style="left:180px;top:85px">Active Since: Jul 25 2023 13:12</span>
      </div>
      <div class="card card--r" style="top:290px;height:94px">
        <svg class="at" style="left:12px;top:28px" width="46" height="40"><use href="#i-files"/></svg>
        <span class="at cm h16" style="left:180px;top:20px">MY CUSTOM CAMPAIGN</span>
        <span class="at cm small" style="left:180px;top:39px">this is my custom campaign for finding i</span>
        <span class="at big big--w mid" style="left:68px;top:63px">0</span>
        <span class="at small mid" style="left:92px;top:55px">Active</span>
        <span class="at mid" style="left:92px;top:68px;font-size:12px;font-weight:700;color:var(--white)">FILES AND HONEYTOKENS</span>
        <span class="at cm tiny" style="left:175px;top:85px">Active Since: Jul 25 2023 13:12</span>
      </div>
    </main>
  </div>
</section>

<!-- Overview screen -->
<section class="screen screen--overview">
  <div class="app">
    <header class="topbar"><span class="brand-dot"></span><span class="brand-name">PlumVesta</span></header>
    <nav class="sidebar">
      <div class="nav-item nav-item--home"><svg class="ico"><use href="#i-home"/></svg>HOME</div>
      <div class="nav-item"><svg class="ico"><use href="#i-bell"/></svg>ALL ALERTS</div>
      <div class="nav-item" style="margin-bottom:0"><svg class="ico"><use href="#i-gear"/></svg>MANAGE</div>
      <div class="nav-item nav-item--group" style="padding-left:43px">Campaigns<span class="trail" style="font-weight:700;font-size:14px">+</span></div>
      <div class="nav-item nav-item--campaign"><svg class="ico"><use href="#i-files"/></svg>MY CUSTOM CAMPAIGN<svg class="trail" width="11" height="7"><use href="#i-chev-up"/></svg></div>
      <div class="nav-item nav-item--sub nav-item--active">OVERVIEW</div>
      <div class="nav-item nav-item--sub">FILE &amp; HONEYTOKENS</div>
      <div class="nav-item nav-item--sub">RESOURCES</div>
      <div class="nav-item nav-item--sub">ALERTS</div>
      <div class="nav-item nav-item--sub" style="margin-bottom:6px">SETTINGS</div>
      <div class="nav-item nav-item--campaign nav-item--plain"><svg class="ico"><use href="#i-files"/></svg>Default Campaign<svg class="trail" width="11" height="7"><use href="#i-chev-down"/></svg></div>
    </nav>
    <div class="page-head"><span class="page-crumb">MY CUSTOM CAMPAIGN</span><span class="page-title">OVERVIEW</span></div>
    <main class="panel">
      <span class="label" style="left:29px;top:26px">TEAMSPACE</span>
      <div class="team-box" style="top:41px"><div class="team-name">MY CUSTOM CAMPAIGN</div><div class="team-desc">This is my custom campaign for finding i</div></div>

      <span class="label" style="left:29px;top:116px">CAMPAIGN ORGANAIZATION</span>
      <span class="label" style="left:343px;top:116px">FILES &amp; HONEYTOKENS</span>
      <div class="card card--l" style="top:128px;height:71px">
        <svg class="at" style="left:31px;top:10px" width="18" height="16"><use href="#i-folder"/></svg>
        <svg class="at" style="left:205px;top:5px" width="30" height="22"><use href="#i-people"/></svg>
        <span class="at big big--w mid" style="left:244px;top:16px">86</span>
        <span class="at cm bold10" style="left:155px;top:40px">SELF-ENABLING DELIVERABLES PROPRIETARY LIMITED</span>
        <span class="at cm small" style="left:155px;top:57px">Standard</span>
      </div>
      <div class="card card--r" style="top:128px;height:71px">
        <svg class="at" style="left:224px;top:4px" width="24" height="24"><use href="#i-tree"/></svg>
        <span class="at big big--w mid" style="left:267px;top:18px">8</span>
        <span class="at cm bold10" style="left:155px;top:40px">UNLEASH BLEEDING-EDGE MINDSHARE</span>
        <span class="at cm small" style="left:155px;top:57px">8 hours ago</span>
      </div>

      <span class="label" style="left:29px;top:216px">SUBSCRIPTION OVERVIEW</span>
      <span class="label" style="left:343px;top:217px">FILES &amp; HONEYTOKENS</span>
      <div class="card card--l" style="top:226px;height:71px">
        <svg class="at" style="left:53px;top:18px" width="27" height="27"><use href="#i-clock"/></svg>
        <span class="at big big--w mid" style="left:85px;top:34px">0</span>
        <svg class="at" style="left:185px;top:18px" width="29" height="25"><use href="#i-folder"/></svg>
        <span class="at big big--w mid" style="left:221px;top:34px">30</span>
        <span class="at cm bold10" style="left:155px;top:60px">STATISTICS</span>
      </div>
      <div class="card card--r" style="top:226px;height:71px">
        <svg class="at c" style="left:155px;top:4px;color:var(--ink)" width="24" height="21"><use href="#i-cubes"/></svg>
        <span class="at cm small" style="left:150px;top:36px">Generate a collection of fictional organisations</span>
        <span class="at cm small" style="left:150px;top:51px">Custom templates, uploaded file and logo</span>
      </div>

      <span class="label" style="left:29px;top:310px">ALERTS</span>
      <div class="card card--l" style="top:320px;height:70px">
        <svg class="at c" style="left:155px;top:12px" width="27" height="24"><use href="#i-warn"/></svg>
        <span class="at cm bold10" style="left:155px;top:47px">ALERT STATISTICS WILL APPEAR JHERE</span>
      </div>
    </main>
  </div>
</section>

</body>
</html>
```